Custom unique Stationary design for Logistics company

We need a custom, unique , elegant and luxurious full stationary design using our new logo, following these guidelines:
1- Business card: double sided, both sides uses the navy blue as the background main color (same as the code of the navy blue used in our logo).
2- envelope and folder: also use the same navy blue as the main background color.
3- book cover( notepad cover) : same thing with the navy blue
4- letterhead: feel free to use the combination of the colors in our logo.
5- rest of the items are up to your creativity

Target Market(s)

corporates and other businesses

Industry/Entity Type

Logistics and heavy machines contractors

Requirements
Must have
• Letterhead, business card, envelope, notepad cover, paper, file
Nice to have
• navy blue to be main background color for business card, envelope, notepad cover

```html
<!DOCTYPE html>
<html lang="en">
<head>
<meta charset="utf-8">
<title>Meridian Freight Group — Stationery</title>
<link href="https://fonts.googleapis.com/css2?family=Montserrat:wght@500;700;800&family=Open+Sans:wght@400;600&display=swap" rel="stylesheet">
<style>
:root{
  --navy:#1d4f72;
  --navy-deep:#163f5c;
  --orange:#e2562b;
  --paper:#fbfbfc;
  --ink:#3b3f44;
  --muted:#8a9098;
  --stage-1:#e6e7e9;
  --stage-2:#dcdde0;
  --stage-3:#e9e9eb;
}
*{box-sizing:border-box;margin:0;padding:0}
html,body{width:1200px;height:5248px;overflow:hidden}
body{font-family:"Open Sans",Arial,sans-serif;color:var(--ink);position:relative;background:var(--stage-1)}
.section{position:absolute;left:0;width:1200px}
.cards{top:0;height:884px;background:var(--stage-1)}
.letter-stage{top:884px;height:1181px;background:#ececee;border-top:2px solid #d2d3d6}
.envelopes{top:2065px;height:1450px;background:var(--stage-2);border-top:2px solid #cfd0d3}
.folder-stage{top:3515px;height:865px;background:radial-gradient(ellipse at 50% 40%,#f4f4f5,#c9cacd)}
.notebook-stage{top:4380px;height:868px;background:var(--stage-3)}

/* brand name block */
.brand{display:flex;flex-direction:column;align-items:center;font-family:"Montserrat",Arial,sans-serif}
.brand-row{display:flex;align-items:center;gap:.18em}
.brand-name{font-weight:800;letter-spacing:.02em;line-height:1}
.brand-dot{width:.28em;height:.28em;border-radius:50%;background:var(--orange)}
.brand-tag{font-weight:700;letter-spacing:.08em;text-transform:uppercase;margin-top:.35em}
.on-navy .brand-name,.on-navy .brand-tag{color:#fff}
.on-paper .brand-name{color:var(--navy)}
.on-paper .brand-tag{color:var(--navy)}

/* business cards */
.card{position:absolute;width:520px;height:300px;background:var(--navy);border-bottom:4px solid var(--orange);box-shadow:0 10px 24px rgba(0,0,0,.22)}
.card-front{left:60px;top:292px;display:flex;align-items:center;justify-content:center}
.card-front .brand{font-size:64px}
.card-front .brand-tag{font-size:10px}
.card-back{left:620px;top:292px;color:#fff}
.card-back .person{position:absolute;left:34px;top:150px}
.person-name{font-family:"Montserrat",Arial,sans-serif;font-weight:700;color:var(--orange);font-size:17px;text-transform:uppercase;letter-spacing:.03em}
.person-role{font-size:13px;color:#fff;margin-bottom:10px}
.contact-line{display:flex;align-items:center;gap:7px;font-size:12px;line-height:20px;color:#fff}
.contact-line svg{width:12px;height:12px;flex:none}
.card-back .brand{position:absolute;right:34px;top:36px;font-size:40px}
.card-back .brand-tag{font-size:7px}
.card-back .divider{position:absolute;left:34px;right:34px;top:128px;height:1px;background:rgba(255,255,255,.45)}
.card-back .address{position:absolute;right:34px;top:150px;text-align:right;font-size:12px;line-height:18px}
.card-back .address .company{color:var(--orange)}

/* letterhead */
.letterhead{position:absolute;left:228px;top:174px;width:642px;height:897px;background:var(--paper);box-shadow:0 6px 22px rgba(0,0,0,.18);padding:56px 58px 0}
.letterhead .brand{font-size:56px}
.letterhead .brand-tag{font-size:8px}
.letter-body{margin-top:62px;font-size:11.4px;line-height:17px;color:#55595e;text-align:justify}
.letter-body p{margin-bottom:17px}
.signature{display:block;margin:8px 0 0 4px}
.letter-foot{position:absolute;left:58px;right:58px;bottom:44px;display:flex;justify-content:space-between;font-size:13.5px;line-height:18px;color:#44484d}
.letter-foot .addr{text-align:right}
.letter-foot .contact-line{color:#44484d;font-size:13.5px;line-height:18px}
.letter-foot svg{width:12px;height:12px}

/* envelopes */
.envelope{position:absolute;width:438px;background:#fff;box-shadow:0 4px 14px rgba(0,0,0,.22)}
.env-front .brand{position:absolute;left:46px;top:44px;font-size:42px;align-items:flex-start}
.env-front .brand-tag{font-size:6px}
.env-front .return{position:absolute;left:46px;top:108px;font-size:8px;line-height:10px;color:var(--muted)}
.env-window{position:absolute;left:46px;width:156px;height:72px;border:1.5px solid #9aa0a6;border-radius:6px;background:#fafafa}
.env-back .flap{position:absolute;left:0;top:0;width:100%;height:76px}
.env-back .brand{position:absolute;left:0;right:0;top:22px;font-size:32px}
.env-back .brand-tag{font-size:5px}
.env-lg{height:625px;top:128px}
.env-md{height:315px;top:780px}
.env-sm{height:205px;top:1115px}
.env-left{left:143px}
.env-right{left:618px}
.env-md.env-front .brand{left:34px;top:36px;font-size:36px}
.env-md.env-front .return{left:34px;top:92px}
.env-sm.env-front .brand{left:30px;top:24px;font-size:32px}
.env-sm.env-front .return{left:30px;top:72px;font-size:7px;line-height:9px}

/* folder */
.folder{position:absolute;left:200px;top:170px;width:800px;height:540px;display:flex;box-shadow:0 16px 34px rgba(0,0,0,.25)}
.folder-back{width:400px;height:100%;background:linear-gradient(160deg,var(--navy),var(--navy-deep));position:relative;color:rgba(255,255,255,.75)}
.folder-back .imprint{position:absolute;left:40px;bottom:44px;font-size:10px;line-height:15px}
.folder-front{width:400px;height:100%;background:#fff;position:relative;display:flex;align-items:center;justify-content:center}
.folder-front .brand{font-size:74px;margin-top:-60px}
.folder-front .brand-tag{font-size:10px}
.folder-front .url{position:absolute;right:40px;bottom:48px;font-family:"Montserrat",Arial,sans-serif;font-weight:700;font-size:10px;color:var(--navy);letter-spacing:.05em;text-transform:uppercase}

/* notebook */
.notebook-page{position:absolute;left:180px;top:190px;width:400px;height:500px;background:#fafafa;box-shadow:0 10px 24px rgba(0,0,0,.2);border-left:6px solid #2d2f33}
.notebook-page .brand{position:absolute;right:40px;top:36px;font-size:26px}
.notebook-page .brand-tag{display:none}
.notebook-cover{position:absolute;left:640px;top:190px;width:380px;height:500px;background:var(--navy);box-shadow:0 12px 26px rgba(0,0,0,.28);border-radius:4px 10px 10px 4px;display:flex;align-items:center;justify-content:center}
.notebook-cover .band{position:absolute;right:46px;top:0;width:10px;height:100%;background:#f1f1f1}
.notebook-cover .brand{font-size:60px;margin-right:30px}
.notebook-cover .brand-tag{font-size:8px}
.notebook-cover .url{position:absolute;left:40px;bottom:40px;font-family:"Montserrat",Arial,sans-serif;font-weight:700;font-size:9px;color:#fff;letter-spacing:.05em}
</style>
</head>
<body>

<section class="section cards">
  <div class="card card-front on-navy">
    <div class="brand"><div class="brand-row"><span class="brand-name">MFG</span><span class="brand-dot"></span></div><div class="brand-tag">Meridian Freight Group</div></div>
  </div>
  <div class="card card-back on-navy">
    <div class="brand"><div class="brand-row"><span class="brand-name">MFG</span><span class="brand-dot"></span></div><div class="brand-tag">Meridian Freight Group</div></div>
    <div class="divider"></div>
    <div class="person">
      <div class="person-name">Owen Harcourt</div>
      <div class="person-role">Managing Director</div>
      <div class="contact-line"><svg viewBox="0 0 12 12"><path d="M2.5 1h2l1 3-1.3 1a6 6 0 0 0 2.8 2.8L8 6.5l3 1v2A1.5 1.5 0 0 1 9.5 11 8.5 8.5 0 0 1 1 2.5 1.5 1.5 0 0 1 2.5 1z" fill="#e2562b"/></svg>304-555-0182</div>
      <div class="contact-line"><svg viewBox="0 0 12 12"><rect x="1" y="2.5" width="10" height="7" rx="1" fill="#e2562b"/><path d="M1.5 3l4.5 3.5L10.5 3" stroke="#1d4f72" fill="none"/></svg>info@meridianfreight.com</div>
      <div class="contact-line"><svg viewBox="0 0 12 12"><circle cx="6" cy="6" r="4.5" stroke="#e2562b" stroke-width="1.4" fill="none"/><path d="M1.5 6h9M6 1.5c2 2.5 2 6.5 0 9M6 1.5c-2 2.5-2 6.5 0 9" stroke="#e2562b" fill="none"/></svg>www.meridianfreight.com</div>
    </div>
    <div class="address"><div class="company">Meridian Freight Group</div>48 Harbor Lane, Suite 210<br>Linden, WV 25390</div>
  </div>
</section>

<section class="section letter-stage">
  <article class="letterhead on-paper">
    <div class="brand"><div class="brand-row"><span class="brand-name">MFG</span><span class="brand-dot"></span></div><div class="brand-tag">Meridian Freight Group</div></div>
    <div class="letter-body">
      <p>Dear customer,</p>
      <p>Lorem ipsum dolor sit amet, consectetur adipisicing elit, sed do eiusmod tempor incididunt ut labore et dolore magna aliqua. Ut enim ad minim veniam, quis nostrud exercitation ullamco laboris nisi ut aliquip ex ea commodo consequat. Duis aute irure dolor in reprehenderit in voluptate velit esse cillum dolore eu fugiat nulla pariatur. Excepteur sint occaecat cupidatat non proident, sunt in culpa qui officia deserunt mollit anim id est laborum.</p>
      <p>Lorem ipsum dolor sit amet, consectetur adipisicing elit, sed do eiusmod tempor incididunt ut labore et dolore magna aliqua. Ut enim ad minim veniam, quis nostrud exercitation ullamco laboris nisi ut aliquip ex ea commodo consequat. Duis aute irure dolor in reprehenderit in voluptate velit esse cillum dolore eu fugiat nulla pariatur. Excepteur sint occaecat cupidatat non proident, sunt in culpa qui officia deserunt mollit anim id est laborum.</p>
      <p>Lorem ipsum dolor sit amet, consectetur adipisicing elit, sed do eiusmod tempor incididunt ut labore et dolore magna aliqua. Ut enim ad minim veniam, quis nostrud exercitation ullamco laboris nisi ut aliquip ex ea commodo consequat. Duis aute irure dolor in reprehenderit in voluptate velit esse cillum dolore eu fugiat nulla pariatur. Excepteur sint occaecat cupidatat non proident, sunt in culpa qui officia deserunt mollit anim id est laborum.</p>
      <p>Lorem ipsum dolor sit amet, consectetur adipisicing elit, sed do eiusmod tempor incididunt ut labore et dolore magna aliqua. Ut enim ad minim veniam, quis nostrud exercitation ullamco laboris nisi ut aliquip ex ea commodo consequat. Duis aute irure dolor in reprehenderit.</p>
      <p>Yours Sincerely,</p>
      <svg class="signature" width="80" height="70" viewBox="0 0 80 70"><path d="M14 20c6 8 4 30-4 40M10 42c10-8 22-8 24 2s-8 10-10 4 10-14 16-6 2 18 0 20M44 18c-2 14-2 30 2 40 4-12 10-20 18-22" stroke="#222" stroke-width="1.4" fill="none"/></svg>
    </div>
    <div class="letter-foot">
      <div>
        <div class="contact-line"><svg viewBox="0 0 12 12"><path d="M2.5 1h2l1 3-1.3 1a6 6 0 0 0 2.8 2.8L8 6.5l3 1v2A1.5 1.5 0 0 1 9.5 11 8.5 8.5 0 0 1 1 2.5 1.5 1.5 0 0 1 2.5 1z" fill="#e2562b"/></svg>203-555-0147</div>
        <div class="contact-line"><svg viewBox="0 0 12 12"><rect x="1" y="2.5" width="10" height="7" rx="1" fill="#e2562b"/><path d="M1.5 3l4.5 3.5L10.5 3" stroke="#fff" fill="none"/></svg>info@meridianfreight.com</div>
        <div class="contact-line"><svg viewBox="0 0 12 12"><circle cx="6" cy="6" r="4.5" stroke="#e2562b" stroke-width="1.4" fill="none"/><path d="M1.5 6h9M6 1.5c2 2.5 2 6.5 0 9M6 1.5c-2 2.5-2 6.5 0 9" stroke="#e2562b" fill="none"/></svg>www.meridianfreight.com</div>
      </div>
      <div class="addr">Meridian Freight Group<br>16 Cedar Quay Road<br>Brookfield, ON L5T 3K8</div>
    </div>
  </article>
</section>

<section class="section envelopes">
  <div class="envelope env-lg env-left env-front on-paper">
    <div class="brand"><div class="brand-row"><span class="brand-name">MFG</span><span class="brand-dot"></span></div><div class="brand-tag">Meridian Freight Group</div></div>
    <div class="return">Meridian Freight Group<br>48 Harbor Lane, Suite 210<br>Linden, WV 25390</div>
    <div class="env-window" style="top:150px"></div>
  </div>
  <div class="envelope env-lg env-right env-back on-navy">
    <svg class="flap" viewBox="0 0 438 76" preserveAspectRatio="none"><path d="M0 0H438L424 56Q422 64 412 64H26Q16 64 14 56Z" fill="#1d4f72"/></svg>
    <div class="brand"><div class="brand-row"><span class="brand-name">MFG</span><span class="brand-dot"></span></div><div class="brand-tag">Meridian Freight Group</div></div>
  </div>

  <div class="envelope env-md env-left env-front on-paper">
    <div class="brand"><div class="brand-row"><span class="brand-name">MFG</span><span class="brand-dot"></span></div><div class="brand-tag">Meridian Freight Group</div></div>
    <div class="return">Meridian Freight Group<br>48 Harbor Lane, Suite 210<br>Linden, WV 25390</div>
    <div class="env-window" style="left:34px;top:128px;width:136px;height:64px"></div>
  </div>
  <div class="envelope env-md env-right env-back on-navy">
    <svg class="flap" viewBox="0 0 438 76" preserveAspectRatio="none"><path d="M0 0H438L424 56Q422 64 412 64H26Q16 64 14 56Z" fill="#1d4f72"/></svg>
    <div class="brand"><div class="brand-row"><span class="brand-name">MFG</span><span class="brand-dot"></span></div><div class="brand-tag">Meridian Freight Group</div></div>
  </div>

  <div class="envelope env-sm env-left env-front on-paper">
    <div class="brand"><div class="brand-row"><span class="brand-name">MFG</span><span class="brand-dot"></span></div><div class="brand-tag">Meridian Freight Group</div></div>
    <div class="return">Meridian Freight Group<br>48 Harbor Lane, Suite 210<br>Linden, WV 25390</div>
    <div class="env-window" style="left:30px;top:126px;width:102px;height:46px"></div>
  </div>
  <div class="envelope env-sm env-right env-back on-navy">
    <svg class="flap" viewBox="0 0 438 76" preserveAspectRatio="none"><path d="M0 0H438L424 56Q422 64 412 64H26Q16 64 14 56Z" fill="#1d4f72"/></svg>
    <div class="brand"><div class="brand-row"><span class="brand-name">MFG</span><span class="brand-dot"></span></div><div class="brand-tag">Meridian Freight Group</div></div>
  </div>
</section>

<section class="section folder-stage">
  <div class="folder">
    <div class="folder-back">
      <div class="imprint">Meridian Freight Group<br>16 Cedar Quay Road, Brookfield, ON L5T 3K8<br>203-555-0147 · info@meridianfreight.com<br>www.meridianfreight.com</div>
    </div>
    <div class="folder-front on-paper">
      <div class="brand"><div class="brand-row"><span class="brand-name">MFG</span><span class="brand-dot"></span></div><div class="brand-tag">Meridian Freight Group</div></div>
      <div class="url">www.meridianfreight.com</div>
    </div>
  </div>
</section>

<section class="section notebook-stage">
  <div class="notebook-page on-paper">
    <div class="brand"><div class="brand-row"><span class="brand-name">MFG</span><span class="brand-dot"></span></div><div class="brand-tag">Meridian Freight Group</div></div>
  </div>
  <div class="notebook-cover on-navy">
    <div class="brand"><div class="brand-row"><span class="brand-name">MFG</span><span class="brand-dot"></span></div><div class="brand-tag">Meridian Freight Group</div></div>
    <div class="band"></div>
    <div class="url">www.meridianfreight.com</div>
  </div>
</section>

</body>
</html>
```